Social responsible Renewable Energy company

We at brivoX are an independent power producer company founded in 2021 that handles large scale deployment of Renewable Energy and carbon neutral Energy as a service model. We offer turnkey solutions using solar panel systems and this could be incorporated in our business cards. You can also find our logo in the documents provided. Another key issue is that the business cards will be printed on recicled paper, not sure if this is a limitation in deciding the design. The recycled sign should also be added on the business card and stating that the paper used was recycled. Our website is www.mybrivox-example.com. It should also be very professional, not too dreamy but still needs to capture your imagination. We are really excited to get your ideas !

Target Market(s)

Renewable Energy market

Contact Information for Business Card

The business card will be printed on recycled paper. Name of the company is brivoX. Website is www.mybrivox-example.com

Requirements
Nice to have
• Our motto: Powered by renewable, driven by people.

```html
<!DOCTYPE html>
<html lang="en">
<head>
<meta charset="utf-8">
<title>brivoX business card</title>
<link rel="stylesheet" href="https://fonts.googleapis.com/css2?family=Open+Sans:wght@400;600;700&display=swap">
<style>
  :root {
    --backdrop: #e6e5e3;
    --kraft: #bba98c;
    --kraft-edge: #a8977a;
    --ink: #2f2f31;
    --ink-soft: #3d3b38;
    --emboss: #ab9a7e;
  }
  * { box-sizing: border-box; margin: 0; padding: 0; }
  html, body {
    width: 1200px; height: 801px; overflow: hidden;
    background: var(--backdrop);
    font-family: "Open Sans", Arial, sans-serif;
    color: var(--ink);
  }
  .sheet {
    width: 1200px; height: 801px;
    display: flex; align-items: center; justify-content: center; gap: 40px;
  }
  .card {
    position: relative;
    width: 540px; height: 309px;
    background: var(--kraft);
    border: 1px solid var(--kraft-edge);
  }
  /* front */
  .brand-block {
    position: absolute; left: 40px; top: 0; bottom: 0; width: 230px;
    display: flex; align-items: center;
  }
  .brand-name {
    font-weight: 700; font-size: 50px; letter-spacing: -1px; color: var(--ink);
  }
  .divider {
    position: absolute; left: 290px; top: 40px; width: 1px; height: 132px;
    background: var(--ink-soft);
  }
  .details {
    position: absolute; left: 306px; top: 40px; right: 16px;
    font-size: 13px; line-height: 1.35; color: var(--ink-soft);
  }
  .person-name { font-weight: 700; font-size: 17px; letter-spacing: .5px; color: var(--ink); }
  .person-role { font-size: 13px; margin-bottom: 10px; }
  .address { margin-bottom: 10px; }
  .contact-row { display: flex; align-items: center; gap: 6px; font-size: 12.5px; }
  .contact-row svg { width: 10px; height: 10px; flex: none; fill: var(--ink); }
  .cert-badges {
    position: absolute; left: 40px; bottom: 26px;
    display: flex; align-items: flex-end; gap: 10px;
  }
  .badge-recycled { width: 18px; height: 18px; border-radius: 50%; border: 2px solid var(--ink-soft); }
  .badge-cert { width: 44px; height: 50px; border: 2px solid var(--ink-soft); border-radius: 4px; }
  /* back */
  .emblem {
    position: absolute; left: 50%; top: 92px; width: 104px; height: 104px;
    margin-left: -52px; border-radius: 50%;
    border: 3px solid var(--emboss);
  }
  .motto {
    position: absolute; left: 0; right: 0; bottom: 40px;
    text-align: center; font-size: 15px; color: var(--ink-soft);
  }
</style>
</head>
<body>
<main class="sheet">
  <section class="card card-front">
    <div class="brand-block"><span class="brand-name">brivoX</span></div>
    <div class="divider"></div>
    <div class="details">
      <p class="person-name">DANIEL MARLOW</p>
      <p class="person-role">President</p>
      <p class="address">1180 Harbor View Lane<br>Seacliff CA 90000</p>
      <p class="contact-row">
        <svg viewBox="0 0 10 10" aria-hidden="true"><path d="M2 0h2l1 3-1.5 1a6 6 0 0 0 2.5 2.5L7 5l3 1v2a2 2 0 0 1-2 2A8 8 0 0 1 0 2a2 2 0 0 1 2-2z"/></svg>
        555-014-2876</p>
      <p class="contact-row">
        <svg viewBox="0 0 10 10" aria-hidden="true"><path d="M0 2h10v6H0z M0 2l5 3.5L10 2" /></svg>
        dmarlow@mybrivox-example.com</p>
      <p class="contact-row">
        <svg viewBox="0 0 10 10" aria-hidden="true"><circle cx="5" cy="5" r="5"/></svg>
        www.mybrivox-example.com</p>
    </div>
    <div class="cert-badges">
      <span class="badge-recycled" role="img" aria-label="Recycled paper mark"></span>
      <span class="badge-cert" role="img" aria-label="Paper certification badge"></span>
    </div>
  </section>
  <section class="card card-back">
    <span class="emblem" aria-hidden="true"></span>
    <p class="motto">Powered by renewable, driven by people.</p>
  </section>
</main>
</body>
</html>
```